We need letterhead, Business Cards, and envelops designed. We have attached a design of our logo and a sample of letterhead idea that was started but never perfected, it is only an idea for the letterhead if you can design something better we may love that also we are open to change.
We want a design that looks professional in style. we are a non profit trade association in the construction industry. the green color in the attached design represent green building, and we like that. also if you just want to enhance the letterhead sample that we attached that would be fine also.
Thanks and good luck
also the name that should show on the first business cards should be Morgan Feltwick, Director are web address is www.pvtrn.org

```html
<!DOCTYPE html>
<html lang="en">
<head>
<meta charset="utf-8">
<title>PVTRN Letterhead</title>
<link rel="stylesheet" href="https://fonts.googleapis.com/css2?family=Didact+Gothic&display=swap">
<style>
  :root {
    --sidebar-black: #000000;
    --paper-white: #ffffff;
    --ink-white: #f2f2f2;
    --leaf-green: #447b1d;
    --brand-black: #111111;
  }
  html, body {
    margin: 0;
    padding: 0;
    overflow: hidden;
    background: var(--paper-white);
  }
  .letterhead {
    position: relative;
    width: 927px;
    height: 1200px;
    background: var(--paper-white);
    overflow: hidden;
    font-family: "Didact Gothic", "Century Gothic", sans-serif;
  }
  .sidebar {
    position: absolute;
    left: 0;
    top: 0;
    width: 219px;
    height: 1200px;
    background: var(--sidebar-black);
  }
  .address {
    position: absolute;
    left: 33px;
    top: 139px;
    margin: 0;
    font-style: normal;
    font-size: 13px;
    line-height: 18.5px;
    letter-spacing: 1.6px;
    color: var(--ink-white);
  }
  .contact-list {
    position: absolute;
    left: 33px;
    top: 229px;
    margin: 0;
    padding: 0;
    list-style: none;
    font-size: 13px;
    line-height: 18.5px;
    letter-spacing: 1.9px;
    color: var(--ink-white);
  }
  .contact-item {
    display: flex;
    align-items: center;
  }
  .contact-icon {
    width: 10px;
    height: 10px;
    margin-right: 24px;
    flex: none;
  }
  .brand {
    position: absolute;
    left: 262px;
    top: 92px;
    display: flex;
    align-items: center;
    gap: 14px;
  }
  .brand-mark {
    width: 22px;
    height: 22px;
    background: var(--leaf-green);
  }
  .brand-name {
    font-size: 72px;
    line-height: 1;
    letter-spacing: 2px;
    color: var(--brand-black);
  }
</style>
</head>
<body>
  <main class="letterhead">
    <aside class="sidebar">
      <address class="address">
        address<br>
        4321 first street<br>
        anytown, State ZIP
      </address>
      <ul class="contact-list">
        <li class="contact-item">
          <svg class="contact-icon" viewBox="0 0 10 10" aria-label="Phone">
            <path d="M1 3.5 Q5 0.5 9 3.5 L8 5 L6.5 4.2 L6.5 3.3 Q5 2.8 3.5 3.3 L3.5 4.2 L2 5 Z" fill="none" stroke="var(--leaf-green)" stroke-width="1"/>
            <rect x="2" y="5.5" width="6" height="3.5" rx="0.6" fill="none" stroke="var(--leaf-green)" stroke-width="1"/>
          </svg>
          <span>123-456-7890</span>
        </li>
        <li class="contact-item">
          <svg class="contact-icon" viewBox="0 0 10 10" aria-label="Fax">
            <rect x="2.5" y="0.8" width="5" height="3" fill="none" stroke="var(--leaf-green)" stroke-width="1"/>
            <rect x="0.8" y="3.8" width="8.4" height="3.6" rx="0.6" fill="none" stroke="var(--leaf-green)" stroke-width="1"/>
            <rect x="2.5" y="6.4" width="5" height="2.8" fill="none" stroke="var(--leaf-green)" stroke-width="1"/>
          </svg>
          <span>123-456-7891</span>
        </li>
        <li class="contact-item">
          <svg class="contact-icon" viewBox="0 0 10 10" aria-label="Website">
            <circle cx="5" cy="5" r="4.2" fill="none" stroke="var(--leaf-green)" stroke-width="1"/>
            <ellipse cx="5" cy="5" rx="1.8" ry="4.2" fill="none" stroke="var(--leaf-green)" stroke-width="0.8"/>
            <line x1="0.8" y1="5" x2="9.2" y2="5" stroke="var(--leaf-green)" stroke-width="0.8"/>
          </svg>
          <span>www.pvtrn.org</span>
        </li>
      </ul>
    </aside>

    <header class="brand">
      <span class="brand-name">PVTRN</span>
      <span class="brand-mark"></span>
    </header>
  </main>
</body>
</html>
```